Current website re-design to a updated look and feel.

We currently have a website www.brightlanefreight.com that we want to give an updated look and feel to. We are a logistics company that competes with Pellwick, Dm Harrowgate, Quill but on a smaller scale. We want something fresh and updated. We have two locations one in downtown Chicago, IL and one in Palatine IL. We are a fun group that also gets the job done. We know we need pictures of both locations and possibly a video, but we need fresh design ideas. The 'who we are' page is really the only page that we currently want to keep. The 'what we do' page needs to be completely re-done from a look and feel for sure.

Target Market(s)

Anyone who uses Truck transportation to move their product. Mainly US manufacturers.

Industry/Entity Type

Logistics

Number of Pages Required

5+ page

Font styles to use
Sans Serif

Colors
5c91c4
0355a3
d0dfed

Requirements
Must have
• The new design must entice people to want to do business with us. The design must have locations for pictures and at least one video which we know we will have to provide. Design must be easy to navigate.

```html
<!DOCTYPE html>
<html lang="en">
<head>
<meta charset="utf-8">
<title>Brightlane Freight</title>
<link rel="stylesheet" href="https://fonts.googleapis.com/css2?family=Alegreya+SC:wght@400;500&family=Lato:wght@400;700;900&family=Open+Sans:wght@400;600;700&display=swap">
<style>
:root{
  --blue:#0355a3;
  --blue-mid:#5c91c4;
  --blue-pale:#d0dfed;
  --blue-bright:#0b8ed6;
  --sky:#1a8ad4;
  --ink:#333;
  --grey-bg:#ececec;
  --black:#000;
  --white:#fff;
}
*{margin:0;padding:0;box-sizing:border-box}
html,body{width:1200px;height:2922px;overflow:hidden}
body{position:relative;font-family:"Open Sans",Arial,sans-serif;color:var(--ink);background:var(--white)}
.abs{position:absolute}
.caps{font-family:"Alegreya SC",Georgia,serif;font-weight:400}

/* header */
.site-header{left:0;top:0;width:1200px;height:101px;background:var(--white)}
.brand{left:78px;top:18px;display:flex;align-items:center;gap:12px}
.brand-mark{width:22px;height:22px;background:var(--blue)}
.brand-name{font-family:"Open Sans",sans-serif;font-weight:600;font-size:44px;color:var(--blue);letter-spacing:-1px}
.main-nav{left:458px;top:56px;display:flex;gap:26px;font-family:"Alegreya SC",Georgia,serif;font-size:17px;color:#555}
.main-nav span.active{color:var(--sky);border-bottom:2px solid var(--sky);padding-bottom:18px}
.login{right:80px;top:10px;font-size:16px;color:#555;display:flex;align-items:center;gap:6px}

/* hero */
.hero{left:0;top:101px;width:1200px;height:600px;background:linear-gradient(180deg,#3c4d5c 0%,#6f7f8a 35%,#7c4a3a 55%,#3d5f74 75%,#2c3b45 100%)}
.hero-title{left:78px;top:165px;font-family:"Lato",sans-serif;font-weight:900;font-size:56px;color:var(--white);letter-spacing:.5px}
.hero-tag{left:80px;top:233px;font-family:"Lato",sans-serif;font-weight:700;font-size:24px;color:var(--white)}
.btn-pill{background:var(--white);color:var(--blue);border-radius:26px;font-family:"Lato",sans-serif;font-weight:900;display:flex;align-items:center;justify-content:center}
.hero-btn{left:78px;top:280px;width:205px;height:50px;font-size:18px}

/* founder */
.founder{left:0;top:595px;width:1200px;height:451px;background:linear-gradient(180deg,#0c86cf 0%,#0a6cb9 60%,var(--blue) 100%);clip-path:polygon(0 0,100% 90px,100% 100%,0 100%)}
.founder-photo{left:76px;top:672px;width:254px;height:320px;border:3px solid var(--white);background:linear-gradient(180deg,#f4f4f4,#d9d9d9)}
.founder-title{left:373px;top:682px;font-size:40px;color:var(--white)}
.founder-text{left:373px;top:752px;width:728px;font-size:15px;line-height:25px;color:var(--white)}
.founder-sign{left:373px;top:953px;font-size:15px;color:var(--white)}

/* vision */
.vision{left:0;top:1046px;width:1200px;height:312px;background:var(--grey-bg)}
.section-title{width:1200px;text-align:center;font-size:40px}
.vision-title{left:0;top:1090px;color:#333}
.vision-title em{font-style:normal;color:var(--blue)}
.vm-icon{width:125px;height:125px;border-radius:50%;border:9px solid var(--sky);background:var(--blue)}
.vm-head{font-size:26px;color:var(--sky)}
.vm-text{width:335px;font-size:15px;line-height:25px;color:#666}
.vm-text u{color:#444}

/* what we do */
.what{left:0;top:1358px;width:1200px;height:629px;background:linear-gradient(160deg,#2b6fb5 0%,#1959a3 50%,#0c4990 100%)}
.what-title{left:0;top:1402px;color:var(--white)}
.what-sub{left:230px;top:1475px;width:740px;text-align:center;font-size:15px;line-height:25px;color:var(--white)}
.vehicles{left:78px;top:1590px;width:450px;height:300px;background:linear-gradient(180deg,#9fb8cf 0%,#e8eef3 50%,#7aa7b8 100%);border-radius:120px 20px 60px 60px;opacity:.9}
.service-tabs{left:566px;top:1570px;width:516px;height:140px;background:var(--sky);border-radius:8px}
.service-tabs::after{content:"";position:absolute;left:40px;bottom:-16px;border:16px solid transparent;border-bottom:0;border-top-color:var(--sky)}
.tab{top:25px;width:90px;height:90px;border:3px solid var(--white);border-radius:10px;background:var(--blue-pale);display:flex;align-items:center;justify-content:center}
.tab.active{background:#111}
.service-head{left:566px;top:1732px;font-size:24px;color:var(--white)}
.service-text{left:566px;top:1780px;width:540px;font-size:15px;line-height:25px;color:var(--white)}
.service-btn{left:563px;top:1880px;width:170px;height:50px;font-size:18px;font-family:"Open Sans",sans-serif;font-weight:600;gap:8px}

/* stats */
.stats{left:0;top:1987px;width:1200px;height:123px;background:var(--grey-bg)}
.stat{top:2000px;width:250px;text-align:center}
.stat-num{font-family:"Alegreya SC",Georgia,serif;font-size:34px;color:var(--blue)}
.stat-label{font-size:15px;line-height:22px;color:#555}
.stat-arrow{top:2028px;width:40px;height:40px;display:flex;align-items:center;justify-content:center}

/* testimonials */
.testimonials{left:0;top:2110px;width:1200px;height:393px;background:linear-gradient(180deg,var(--blue-bright) 0%,#0a6fc0 55%,var(--blue) 100%)}
.testi-title{left:0;top:2152px;color:var(--white)}
.testi-quote{left:0;top:2210px;width:1200px;text-align:center;font-family:Georgia,serif;font-size:80px;line-height:80px;color:var(--white);font-weight:700}
.testi-text{left:180px;top:2290px;width:840px;text-align:center;font-size:15px;line-height:25px;color:var(--white)}
.testi-name{left:0;top:2393px;width:1200px;text-align:center;font-size:15px;font-weight:700;color:var(--white)}
.dots{left:543px;top:2432px;display:flex;gap:12px}
.dots i{width:17px;height:17px;border-radius:50%;background:var(--white)}

/* badges */
.badge{top:2528px;width:167px;height:105px;border:1px solid #ccc;display:flex;align-items:center;justify-content:center}
.badge i{display:block;width:70px;height:70px;border-radius:50%;background:var(--blue-pale)}
.badge i.sq{border-radius:4px;width:110px;height:55px}

/* footer */
.footer{left:0;top:2659px;width:1200px;height:209px;background:var(--black)}
.foot-nav{left:80px;top:2688px;display:flex;gap:32px;font-size:15px;color:var(--white)}
.social{right:80px;top:2689px;display:flex;gap:18px}
.social i{width:18px;height:18px;border-radius:50%;background:var(--white)}
.foot-rule{left:78px;top:2736px;width:1044px;height:1px;background:#555}
.contact-title{left:80px;top:2752px;font-size:22px;color:var(--white)}
.contact-item{top:2790px;display:flex;gap:12px;align-items:flex-start;font-size:14px;line-height:22px;color:var(--white)}
.contact-icon{width:42px;height:42px;border-radius:50%;display:flex;align-items:center;justify-content:center;flex:none}
.copyright{left:0;top:2868px;width:1200px;height:54px;background:#2a66a6;color:var(--white);font-size:15px;display:flex;align-items:center;justify-content:center;gap:6px}
</style>
</head>
<body>

<header class="abs site-header">
  <div class="abs brand"><span class="brand-mark"></span><span class="brand-name">Brightlane</span></div>
  <nav class="abs main-nav">
    <span class="active">WHAT WE DO</span><span>HOW WE DO IT</span><span>WHO WE ARE</span><span>TRACKING</span><span>CHAT</span><span>CONTACT</span>
  </nav>
  <div class="abs login">
    <svg width="14" height="16" viewBox="0 0 14 16"><rect x="1" y="7" width="12" height="9" rx="1" fill="#666"/><path d="M4 7V4a3 3 0 0 1 6 0v3" stroke="#666" stroke-width="2" fill="none"/></svg>Login
  </div>
</header>

<section class="abs hero" role="img" aria-label="Photo of a container port with stacked shipping containers and cranes under a grey sky"></section>
<h1 class="abs hero-title">BRIGHTLANE FREIGHT</h1>
<p class="abs hero-tag">Relax. We Got This.</p>
<div class="abs btn-pill hero-btn">REQUEST A QUOTE</div>

<section class="abs founder"></section>
<div class="abs founder-photo" role="img" aria-label="Portrait photo of the company founder"></div>
<h2 class="abs founder-title caps">Welcome From Our Founder</h2>
<p class="abs founder-text">Brightlane Freight welcomes you to our growing family of clients! We have over 26 years of experience in helping people solve their logistics needs from coast-to-coast. We also provide friendly, exceptional service that makes it easy to do business with us. Give us a call today and experience the difference for yourself!<br>"Our service commitment begins from the moment you contact us. We appreciate your trust, and we go the extra mile to ensure that your freight is handled with care and expediency. If an issue comes up, we work tirelessly to resolve it, staying in contact with you until your freight is delivered without issue!"</p>
<p class="abs founder-sign">Let us take the worry out of your logistics. Relax, we've got this! - Marian Totten, Founder</p>

<section class="abs vision"></section>
<h2 class="abs section-title vision-title caps">Brightlane Freight <em>Vision and Mission</em></h2>
<div class="abs vm-icon" style="left:78px;top:1180px" role="img" aria-label="Telescope icon"></div>
<h3 class="abs vm-head caps" style="left:222px;top:1172px">Brightlane Vision</h3>
<p class="abs vm-text" style="left:222px;top:1210px">Brightlane vision is to be the premier third party logistics solution in North America. We will become premier by providing superior customer service, efficient... <u>READ MORE</u></p>
<div class="abs vm-icon" style="left:623px;top:1180px" role="img" aria-label="Rocket icon"></div>
<h3 class="abs vm-head caps" style="left:768px;top:1172px">Brightlane Mission</h3>
<p class="abs vm-text" style="left:768px;top:1210px">Brightlane's mission is to provide the most thorough and satisfying third-party logistics experience for its customers. Brightlane uses leading technologies and an... <u>READ MORE</u></p>

<section class="abs what" role="img" aria-label="Blue-tinted aerial view of a city highway interchange"></section>
<h2 class="abs section-title what-title caps">What We Do</h2>
<p class="abs what-sub">Lorem Ipsum is simply dummy text of the printing and typesetting industry. Lorem Ipsum has been the industry's standard dummy text ever since the 1500s</p>
<div class="abs vehicles" role="img" aria-label="Illustration of a private jet, a coach bus and a silver sedan"></div>
<div class="abs service-tabs">
  <div class="abs tab active" style="left:20px">
    <svg width="44" height="44" viewBox="0 0 44 44" fill="none" stroke="#fff" stroke-width="3"><path d="M8 6h6l6 22h16"/><rect x="18" y="12" width="16" height="12"/><circle cx="22" cy="35" r="3"/><circle cx="34" cy="35" r="3"/></svg>
  </div>
  <div class="abs tab" style="left:150px">
    <svg width="44" height="44" viewBox="0 0 44 44" fill="none" stroke="#111" stroke-width="3"><rect x="8" y="6" width="28" height="28" rx="3"/><path d="M8 18h28"/><circle cx="15" cy="38" r="3"/><circle cx="29" cy="38" r="3"/></svg>
  </div>
  <div class="abs tab" style="left:280px">
    <svg width="44" height="44" viewBox="0 0 44 44" fill="none" stroke="#111" stroke-width="3"><path d="M4 18L22 6l18 12v20H4z"/><rect x="12" y="24" width="20" height="14"/></svg>
  </div>
  <div class="abs tab" style="left:410px">
    <svg width="44" height="44" viewBox="0 0 44 44" fill="none" stroke="#111" stroke-width="3"><path d="M4 12h24v20H4zM28 18h8l5 7v7H28"/><circle cx="12" cy="34" r="3"/><circle cx="33" cy="34" r="3"/></svg>
  </div>
</div>
<h3 class="abs service-head caps">Freight Management</h3>
<p class="abs service-text">We strive for a perfect delivery and promise to be there for anything you may need, every step of the way. Click here to find out more about Freight Management and how we do it..</p>
<div class="abs btn-pill service-btn">READ MORE <span>&raquo;</span></div>

<section class="abs stats"></section>
<div class="abs stat-arrow" style="left:0;background:#111"><svg width="12" height="16" viewBox="0 0 12 16"><path d="M9 2L3 8l6 6" stroke="#fff" stroke-width="2" fill="none"/></svg></div>
<div class="abs stat-arrow" style="left:1160px;background:var(--blue)"><svg width="12" height="16" viewBox="0 0 12 16"><path d="M3 2l6 6-6 6" stroke="#fff" stroke-width="2" fill="none"/></svg></div>
<div class="abs stat" style="left:70px"><div class="stat-num">7</div><div class="stat-label">Average Years of<br>Employment</div></div>
<div class="abs stat" style="left:340px"><div class="stat-num">443,244</div><div class="stat-label">Emails Sent/Received Per<br>Year</div></div>
<div class="abs stat" style="left:610px"><div class="stat-num">500</div><div class="stat-label">Hours of Community Service<br>Per Year</div></div>
<div class="abs stat" style="left:880px"><div class="stat-num">8</div><div class="stat-label">Office Locations<br>Outgrown</div></div>

<section class="abs testimonials"></section>
<h2 class="abs section-title testi-title caps">Tesimonials</h2>
<div class="abs testi-quote">&ldquo;</div>
<p class="abs testi-text">Lorem Ipsum is simply dummy text of the printing and typesetting industry. Lorem Ipsum has been the industry's standard dummy text ever since the 1500s, when an unknown printer took a galley of type and scrambled it to make a type specimen book.</p>
<p class="abs testi-name">- Client Name</p>
<div class="abs dots"><i></i><i></i><i></i><i></i></div>

<div class="abs badge" style="left:78px"><i></i></div>
<div class="abs badge" style="left:253px"><i></i></div>
<div class="abs badge" style="left:428px"><i class="sq"></i></div>
<div class="abs badge" style="left:603px"><i class="sq"></i></div>
<div class="abs badge" style="left:778px"><i></i></div>
<div class="abs badge" style="left:953px"><i class="sq"></i></div>

<footer class="abs footer"></footer>
<nav class="abs foot-nav"><span>What We Do</span><span>How We Do It</span><span>Who We Are</span><span>Tracking</span><span>Chat</span><span>Contact</span></nav>
<div class="abs social" aria-label="Social links"><i></i><i></i><i></i><i></i></div>
<div class="abs foot-rule"></div>
<h3 class="abs contact-title caps">Contact Us</h3>
<div class="abs contact-item" style="left:78px">
  <span class="contact-icon" style="background:var(--blue)"><svg width="16" height="22" viewBox="0 0 16 22"><path d="M8 1a7 7 0 0 1 7 7c0 5-7 13-7 13S1 13 1 8a7 7 0 0 1 7-7z" fill="#fff"/><circle cx="8" cy="8" r="3" fill="var(--blue)"/></svg></span>
  <span>418 W Alder St &nbsp;Suite 210<br>Larkfield, IL &nbsp;60098</span>
</div>
<div class="abs contact-item" style="left:348px">
  <span class="contact-icon" style="background:var(--white)"><svg width="20" height="20" viewBox="0 0 20 20"><path d="M4 1l4 4-2 3a11 11 0 0 0 6 6l3-2 4 4-3 3C9 19 1 11 1 4z" fill="var(--blue)"/></svg></span>
  <span>Office : 847.555.0140<br>Warehouse: 847.555.0142</span>
</div>
<div class="abs contact-item" style="left:618px">
  <span class="contact-icon" style="background:var(--blue)"><svg width="16" height="22" viewBox="0 0 16 22"><path d="M8 1a7 7 0 0 1 7 7c0 5-7 13-7 13S1 13 1 8a7 7 0 0 1 7-7z" fill="#fff"/><circle cx="8" cy="8" r="3" fill="var(--blue)"/></svg></span>
  <span>Chicago, IL<br>address</span>
</div>
<div class="abs contact-item" style="left:888px">
  <span class="contact-icon" style="background:var(--white)"><svg width="20" height="20" viewBox="0 0 20 20"><path d="M4 1l4 4-2 3a11 11 0 0 0 6 6l3-2 4 4-3 3C9 19 1 11 1 4z" fill="var(--blue)"/></svg></span>
  <span>Office : 123.456.7890<br>Warehouse: 123.456.7890</span>
</div>
<div class="abs copyright">&copy; <strong>BRIGHTLANE FREIGHT - 2017.</strong> All Rights Reserved.</div>

</body>
</html>
```